Trade Show Marlow 3x3 booth schel scheme

We would like to have full coverage design for 3x3 booth scheel

2x2 pop up Counter (1200mm wide x 900mm high x 400mm deep)
Our company provides food safety training, consultancy and food safety app service for hospitality businesses.

```html
<!DOCTYPE html>
<html lang="en">
<head>
<meta charset="utf-8">
<title>Marlow – Booth Graphics</title>
<link href="https://fonts.googleapis.com/css2?family=Archivo+Black&family=Montserrat:wght@500;600&display=swap" rel="stylesheet">
<style>
  :root {
    --backdrop: #8eacd6;
    --lime: #cdd630;
    --lime-deep: #6f9a12;
    --cream: #fbfbe3;
    --charcoal: #2e2e2e;
    --ink: #111111;
    --white: #ffffff;
    --badge: #22a82c;
  }
  * { margin: 0; padding: 0; box-sizing: border-box; }
  html, body { width: 1200px; height: 905px; overflow: hidden; }
  body { background: var(--backdrop); position: relative; font-family: "Montserrat", sans-serif; }

  .panel { position: absolute; overflow: hidden; }
  .display { font-family: "Archivo Black", sans-serif; letter-spacing: -0.04em; line-height: 1; position: absolute; white-space: nowrap; }
  .wordmark { position: absolute; font-family: "Montserrat", sans-serif; font-weight: 500; letter-spacing: 0.22em; line-height: 1; white-space: nowrap; }

  /* Promise panel */
  .promise { left: 53px; top: 52px; width: 537px; height: 444px; background: var(--cream); }
  .promise__field { position: absolute; left: 194px; top: 0; width: 323px; height: 444px; background: var(--lime); }
  .promise__photo { position: absolute; left: 36px; top: 36px; width: 170px; height: 408px; background: linear-gradient(180deg, #c9a98a 0%, #b89575 55%, #2a2522 80%, #1e1b19 100%); border-radius: 80px 80px 0 0; }
  .promise .wordmark { left: 213px; top: 48px; font-size: 38px; color: var(--ink); }
  .promise__band { position: absolute; left: 194px; top: 162px; width: 328px; height: 60px; background: var(--lime-deep); }
  .promise__band span { position: absolute; left: 20px; top: 14px; font-size: 29px; color: var(--cream); }
  .promise .peace { left: 212px; top: 222px; font-size: 82px; color: var(--charcoal); }
  .promise .of-box { position: absolute; left: 212px; top: 303px; width: 52px; height: 33px; background: var(--lime-deep); }
  .promise .of-box span { left: 5px; top: 5px; font-size: 24px; color: var(--white); }
  .promise .mind { left: 268px; top: 288px; font-size: 82px; color: var(--charcoal); }
  .promise .bang { left: 455px; top: 270px; font-size: 118px; color: var(--lime-deep); transform: skewX(-10deg); }
  .tick-badge { position: absolute; }

  /* Rating panel */
  .rating { left: 610px; top: 52px; width: 539px; height: 444px; background: var(--cream); }
  .rating__shape { position: absolute; inset: 0; }
  .rating .achieve { left: 35px; top: 70px; font-size: 30px; color: var(--ink); }
  .rating__rule { position: absolute; left: 35px; top: 106px; width: 214px; height: 1px; background: var(--cream); }
  .rating .headline { left: 33px; top: 116px; font-size: 58px; line-height: 45px; color: var(--ink); }
  .rating__tablet { position: absolute; left: 292px; top: 100px; width: 220px; height: 150px; background: #1b1b1b; border-radius: 14px; transform: rotate(5deg) skewX(-8deg); padding: 6px; }
  .rating__tablet div { width: 100%; height: 100%; border-radius: 9px; background: linear-gradient(180deg, var(--lime) 0 8%, #f1f1f1 8% 35%, #e05252 35% 46%, #f4f4f4 46%); }
  .rating__callout { position: absolute; left: 34px; top: 276px; width: 366px; height: 89px; background: var(--ink); }
  .rating__callout::before { content: ""; position: absolute; left: 168px; top: -8px; border: 9px solid transparent; border-top: 0; border-bottom: 9px solid var(--ink); }
  .rating .experts { left: 18px; top: 8px; font-size: 40px; line-height: 36px; color: var(--white); }
  .rating .wordmark { left: 374px; top: 398px; font-size: 26px; color: var(--ink); }

  /* Counter panel */
  .counter { left: 254px; top: 539px; width: 692px; height: 303px; background: var(--charcoal); color: var(--white); text-align: center; }
  .counter .wordmark { left: 0; width: 692px; top: 28px; font-size: 46px; color: var(--white); text-align: center; padding-left: 0.22em; }
  .counter__rule { position: absolute; left: 214px; top: 82px; width: 263px; height: 1.5px; background: var(--white); }
  .counter__tagline { position: absolute; left: 0; width: 692px; top: 97px; font-size: 21px; font-weight: 500; letter-spacing: 0.16em; line-height: 29px; }
  .service { position: absolute; top: 162px; width: 120px; text-align: center; }
  .service svg { display: block; margin: 0 auto; }
  .service__label { display: block; margin-top: 8px; font-size: 12.5px; font-weight: 500; }
  .service--training { left: 157px; }
  .service--consult { left: 285px; }
  .service--app { left: 421px; }
  .counter__divider { position: absolute; top: 167px; width: 1px; height: 57px; background: var(--white); }
  .counter__url { position: absolute; left: 248px; top: 260px; width: 194px; height: 23px; border-radius: 12px; background: var(--white); color: var(--ink); font-size: 12px; font-weight: 500; line-height: 23px; }
</style>
</head>
<body>

<section class="panel promise">
  <div class="promise__field"></div>
  <div class="promise__photo" role="img" aria-label="Photo of a professional woman in a beige blazer holding a tablet"></div>
  <svg class="tick-badge" style="left:18px;top:133px" width="56" height="56" viewBox="0 0 56 56" aria-hidden="true">
    <circle cx="28" cy="28" r="27" fill="var(--badge)"/>
    <path d="M16 29 l8 8 l16 -17" fill="none" stroke="#fff" stroke-width="6" stroke-linecap="round" stroke-linejoin="round"/>
  </svg>
  <svg class="tick-badge" style="left:453px;top:88px" width="76" height="76" viewBox="0 0 56 56" aria-hidden="true">
    <circle cx="28" cy="28" r="27" fill="var(--badge)"/>
    <path d="M16 29 l8 8 l16 -17" fill="none" stroke="#fff" stroke-width="6" stroke-linecap="round" stroke-linejoin="round"/>
  </svg>
  <div class="wordmark">MARLOW</div>
  <div class="promise__band"><span class="display">OUR PROMISE IS</span></div>
  <div class="display peace">PEACE</div>
  <div class="of-box"><span class="display">OF</span></div>
  <div class="display mind">MIND</div>
  <div class="display bang">!</div>
</section>

<section class="panel rating">
  <svg class="rating__shape" width="539" height="444" viewBox="0 0 539 444" aria-hidden="true">
    <path d="M0 0 H539 V205 C470 330 360 400 230 430 C150 447 70 430 0 390 Z" fill="var(--lime)"/>
  </svg>
  <div class="display achieve">ACHIEVE &amp; MAINTAIN</div>
  <div class="rating__rule"></div>
  <div class="display headline">5 STAR<br>HYGIENE<br>RATING</div>
  <div class="rating__tablet" role="img" aria-label="Tablet showing the hygiene checklist app dashboard"><div></div></div>
  <div class="rating__callout">
    <div class="display experts">WITH EXPERTS<br>AT YOUR SIDE!</div>
  </div>
  <div class="wordmark">MARLOW</div>
</section>

<section class="panel counter">
  <div class="wordmark">MARLOW</div>
  <div class="counter__rule"></div>
  <div class="counter__tagline">FOOD HYGIENE AND<br>HEALTH SAFETY</div>

  <div class="service service--training">
    <svg width="52" height="44" viewBox="0 0 52 44" aria-hidden="true">
      <circle cx="33" cy="18" r="17" fill="var(--lime)"/>
      <g fill="none" stroke="#fff" stroke-width="1.6" stroke-linecap="round">
        <rect x="18" y="6" width="22" height="16" rx="1"/>
        <path d="M22 11 h14 M22 15 h14 M22 19 h9"/>
        <circle cx="11" cy="15" r="3"/>
        <path d="M7 42 V24 h8 l6 -4 M15 24 V42 M11 30 V42 M29 22 V34 M24 42 l5 -8 l5 8"/>
      </g>
    </svg>
    <span class="service__label">Training</span>
  </div>

  <div class="counter__divider" style="left:275px"></div>

  <div class="service service--consult">
    <svg width="52" height="44" viewBox="0 0 52 44" aria-hidden="true">
      <circle cx="33" cy="18" r="17" fill="var(--lime)"/>
      <g fill="none" stroke="#fff" stroke-width="1.6" stroke-linecap="round">
        <circle cx="10" cy="8" r="3"/><circle cx="34" cy="8" r="3"/>
        <rect x="16" y="3" width="12" height="8" rx="1"/>
        <path d="M6 40 V20 h8 l4 6 h16 M38 40 V20 h-8 M12 28 V40 M32 26 V40 M18 26 V40 M26 26 V40"/>
      </g>
    </svg>
    <span class="service__label">Consultancy</span>
  </div>

  <div class="counter__divider" style="left:414px"></div>

  <div class="service service--app">
    <svg width="52" height="44" viewBox="0 0 52 44" aria-hidden="true">
      <circle cx="33" cy="18" r="17" fill="var(--lime)"/>
      <g fill="none" stroke="#fff" stroke-width="1.6" stroke-linecap="round" stroke-linejoin="round">
        <rect x="16" y="2" width="16" height="30" rx="3"/>
        <path d="M20 16 l3 3 l5 -6"/>
        <circle cx="36" cy="8" r="2.5"/><circle cx="36" cy="16" r="2.5"/><circle cx="36" cy="24" r="2.5"/>
        <path d="M10 42 l4 -10 l6 -6 l4 3 l-4 6"/>
      </g>
    </svg>
    <span class="service__label">Safety App</span>
  </div>

  <div class="counter__url">www.marlowsafety.co.uk</div>
</section>

</body>
</html>
```